Cruise Booking Website

Cruise search and booking website

This project is a redesign of a cruise booking website we did a few years ago.

The current website is located here: http://voyage.pylonworks.example/en/

It's not fully functional but gives you ad idea how miserable the old design was.

All the information about cruises, cruise lines, destinations, ports and shore excursions will be similar to http://www.sailquest.example/
Actual search pages (form, results, single result, sailing and cabin selection, ship info, booking) will have EXACTLY the same info as sailquest.example

We like the style of http://harborfleetdesk.example, it's quite modern, good spacing, not overloaded with information. So you can use it as an example of what we like, not what we want as a final result for us. Please, don't copy it. The result should not be possible to resemble the harborfleetdesk.example, because our site has to be unique. This is important!
If you submit a design that clearly reminds another cruise site it will be rejected!

Also the mockup provided is just to give you the basic structure and show what information has to be present on the page. It doesn't mean the layout has to be the same as a mockup. The layout is up to the designer.

I've updated the mockup to be more generic so it doesn't confuse you:
https://files.boxvault.example/s/k7m2qp9wz4hx/Home%20page.png

When you're adding social sharing icons like plazanet/chirpline you have to use chinese ones instead:
https://files.boxvault.example/s/t3nr8vx5lc2e/chinese-social-icons.png
Originals: http://minilk.example/qR7t

We'll start with home page first and after it's approved inner pages can be designed.

I know the cost of the project doesn't look high, but the task is straight forward and doesn't require to be very original, it's better to follow existing design and layout patterns that proved to work well.
That's why I encourage you to choose a template to build the design on top of one of https://themeparlor.example/ themes if it will save the design work, will be easier and faster for you. So it will be more like a customization than a new design from scratch.

Mockups, site map and logo files:
- https://files.boxvault.example/sh/h48dm2rs73fkpw/QvnbW2Xz8e

Website tree:
- https://sheets.papernest.example/document/d/7xPqR2mLw9sTk4VbN8cHj3YzA6eUf5GdKo1iMnBv/edit?usp=sharing
Updates

So far a lot of designs are just copying http://www.harborfleetdesk.example/ - we don't like it!

We like the style of harborfleetdesk.example, it's quite modern, good spacing, not overloaded with information. So you can use it as an example of what we like, not what we want as a final result for us. Please, don't copy it. The result should not be possible to resemble the harborfleetdesk.example, because our site has to be unique. This is important!

Target Market(s)

Chinese travellers

Industry/Entity Type

Build

Requirements
Must have
• * White, blue and red
* Large spacing, not too much information cramped into a small space like sailquest.example or the current website
* More "hidden" info in popups, tabs and so on, so not to many things are visible at the same time
* Compatible with kestrel scaffold styling (for easier coding):
- http://kestrelkit.codeshelf.example/scaffold/index.html
- http://skinmarket.example/
* Feel free to propose to build the design on top of one of https://themeparlor.example/ themes if it will save the design work, will be easier and faster for you

```html
<!DOCTYPE html>
<html lang="en">
<head>
<meta charset="utf-8">
<title>Haiyun Cruises – Cruise Vacations</title>
<link href="https://fonts.googleapis.com/css2?family=Source+Sans+3:ital,wght@0,400;0,600;0,700;1,400;1,600&display=swap" rel="stylesheet">
<style>
:root{
  --bg-deep:#1f5f98;
  --bg-light:#d7e7f3;
  --brand:#1b6aa6;
  --brand-dark:#175b8f;
  --nav:#1c73b4;
  --nav-dark:#135d96;
  --footer:#3b78ad;
  --footer-dark:#2f6a9e;
  --panel:#3c4248;
  --tab:#5d6166;
  --tab-active:#5fb2dc;
  --red:#f3540c;
  --red-light:#ff7a1f;
  --text:#3f4549;
  --muted:#7b8084;
  --white:#ffffff;
  --field:#ebedef;
  --tick:#6aae2b;
}
*{box-sizing:border-box;margin:0;padding:0}
html,body{width:869px;height:1200px;overflow:hidden}
body{
  font-family:"Source Sans 3",Arial,sans-serif;color:var(--text);position:relative;
  background:radial-gradient(ellipse 62% 55% at 50% 30%,var(--bg-light) 0%,#7fb0d6 45%,var(--bg-deep) 100%);
}
.page{position:absolute;left:130px;top:0;width:608px;height:1200px}
.abs{position:absolute}
a{color:inherit;text-decoration:none}
ul{list-style:none}

/* header */
.header{position:absolute;left:0;top:0;width:608px;height:81px;background:var(--white)}
.brand{position:absolute;left:8px;top:22px;display:flex;align-items:center;gap:6px}
.brand-mark{width:34px;height:34px;border-radius:50%;background:var(--brand)}
.brand-name{font-weight:700;font-size:21px;color:var(--brand);line-height:1}
.brand-url{position:absolute;left:48px;top:57px;font-size:7.5px;font-weight:700;color:var(--brand);line-height:1}
.account{position:absolute;left:398px;top:17px;font-size:8px;color:var(--brand);display:flex;align-items:center;gap:6px}
.lang{border:1px solid #c9ced2;border-radius:2px;height:15px;padding:0 5px;display:flex;align-items:center;gap:4px;color:var(--text);font-size:7.5px;margin-left:2px}
.lang i{width:10px;height:7px;background:#2a4f8e;display:block}
.social{display:flex;gap:3px;margin-left:4px}
.social span{width:16px;height:16px;border-radius:3px;background:#4b8ac4;display:block}
.phone{position:absolute;right:14px;top:38px;text-align:right;font-weight:700;color:var(--brand);font-size:12px}
.call{position:absolute;right:14px;top:54px;font-size:12.5px;color:var(--text)}

/* nav */
.nav{position:absolute;left:0;top:81px;width:608px;height:24px;background:linear-gradient(var(--nav),var(--nav-dark))}
.nav a{position:absolute;top:7px;font-size:7.5px;font-weight:700;color:var(--white)}
.search{position:absolute;left:492px;top:5px;width:111px;height:14px;border-radius:2px;background:#e8eef3;font-size:6px;color:var(--muted);padding:3px 6px}
.search svg{position:absolute;right:4px;top:2px}

/* hero */
.hero{position:absolute;left:0;top:105px;width:608px;height:310px;
  background:linear-gradient(180deg,#b9dcf0 0%,#d8ecf6 35%,#8aa07a 62%,#5f6e58 82%,#6b6258 100%)}
.hero-tag{position:absolute;left:251px;top:108px;color:var(--brand-dark);font-style:italic;font-weight:600;line-height:1.1}
.hero-tag .l1{font-size:17.5px;display:block}
.hero-tag .l2{font-size:23px;display:block;margin-top:3px}
.arrow{position:absolute;top:138px;width:18px;height:18px;border-radius:50%;background:rgba(255,255,255,.45)}

.finder{position:absolute;left:421px;top:21px;width:172px;height:269px;background:rgba(52,56,60,.92);color:var(--white)}
.finder h2{position:absolute;left:0;top:12px;width:100%;text-align:center;font-size:12px;font-weight:700}
.finder .rule{position:absolute;left:13px;top:31px;width:149px;height:1px;background:#70767c}
.finder label{position:absolute;font-size:6.5px;font-weight:600;text-transform:uppercase}
.select{position:absolute;height:16px;border-radius:2px;background:linear-gradient(#f2f3f4,#c9cdd0);color:var(--text);font-size:6px;padding:4px 6px;text-transform:uppercase}
.select::after{content:"";position:absolute;right:6px;top:6px;border:3.5px solid transparent;border-top:4px solid #444}
.senior{position:absolute;left:13px;top:214px;font-size:6.5px;font-weight:600;display:flex;align-items:center;gap:5px}
.senior i{width:8px;height:8px;background:#a5d28a;border:1px solid #ddd;display:block}
.btn-search{position:absolute;left:13px;top:233px;width:149px;height:24px;border-radius:2px;background:linear-gradient(var(--red-light),var(--red));font-size:9px;text-align:center;line-height:24px}

/* content band */
.band{position:absolute;left:0;top:415px;width:608px;height:313px;background:var(--white)}
.tab{position:absolute;top:15px;height:23px;font-size:7.5px;color:#d5d7d9;text-align:center;line-height:24px;background:var(--tab);clip-path:polygon(0 0,88% 0,100% 100%,0 100%)}
.tab.active{background:var(--tab-active);color:#0e4a73}
.tab-body{position:absolute;left:10px;top:38px;width:450px;height:261px;border:1px solid #dfe2e4}
.photo-couple{position:absolute;left:14px;top:19px;width:226px;height:138px;background:linear-gradient(180deg,#4aa3d6 0%,#1e8fc4 48%,#2c87b6 68%,#e8ecee 70%,#f3f4f4 100%)}
.photo-shadow{position:absolute;left:24px;top:160px;width:206px;height:12px;border-radius:50%;background:radial-gradient(ellipse at center,rgba(0,0,0,.35),rgba(0,0,0,0) 70%)}
.promise{position:absolute;left:262px;top:25px;width:180px}
.promise h3{font-size:11px;font-weight:700;color:var(--brand)}
.promise p{font-size:6.5px;line-height:1.7;margin-top:4px}
.promise ul{margin-top:8px}
.promise li{font-size:6.5px;height:16.5px;display:flex;align-items:flex-start;gap:5px}
.dots{position:absolute;left:380px;top:241px;display:flex;gap:4px}
.dots i{width:8px;height:8px;border-radius:50%;background:#9ea3a7;display:block}
.dots i:first-child{background:#4b8ac4}

.deals{position:absolute;left:479px;top:15px;width:115px;height:97px;background:linear-gradient(#2d7fbd,var(--brand-dark));border-radius:2px;color:var(--white);text-align:center;font-weight:700;font-size:17px;line-height:1.2;padding-top:16px}
.signup-note{position:absolute;left:479px;top:125px;width:118px;font-size:8px;line-height:1.65;color:var(--brand)}
.field{position:absolute;height:16px;border:1px solid #c8cdd1;border-radius:2px;background:#f8f9fa;font-size:6.5px;color:var(--muted);padding:3px 7px}
.btn-red{position:absolute;left:478px;top:265px;width:63px;height:16px;border-radius:2px;background:linear-gradient(var(--red-light),var(--red));color:var(--white);font-size:7px;text-align:center;line-height:16px}
.contest{position:absolute;font-size:7px;color:var(--brand)}

/* footer */
.footer{position:absolute;left:0;top:728px;width:608px;height:436px;background:var(--footer);color:var(--white)}
.footer h4{position:absolute;font-size:9.5px;font-weight:700}
.footer ul{position:absolute;font-size:6.5px;line-height:13.6px}
.more{position:absolute;height:16px;border:1px solid #8fb5d6;border-radius:2px;font-size:6.5px;line-height:14px;padding:0 9px}
.community{position:absolute;left:306px;top:20px;width:143px;height:275px;background:var(--brand)}
.community .sbtn{position:absolute;left:12px;width:100px;height:12px;border-radius:2px;background:#a9cbe8;color:#23527c;font-size:5.5px;line-height:12px;padding-left:30px}
.community .sbtn i{position:absolute;left:4px;top:2px;width:8px;height:8px;background:#4b7cba;display:block}
.community p{position:absolute;left:12px;top:108px;width:125px;font-size:6px;line-height:1.9}
.community .field{left:12px;width:120px;background:var(--white);border-color:#fff}
.btn-blue{position:absolute;left:12px;top:262px;width:63px;height:16px;border-radius:2px;background:linear-gradient(#69b8e2,#3b94c9);font-size:7px;text-align:center;line-height:16px}
.contact-card{position:absolute;left:469px;top:47px;width:62px;height:60px;background:var(--white);display:flex;align-items:center;justify-content:center}
.contact-card i{width:30px;height:30px;border-radius:50%;background:var(--brand);display:block}
.contact-line{position:absolute;left:469px;font-size:7px;display:flex;align-items:center;gap:5px}
.about-mark{position:absolute;left:468px;top:178px;width:36px;height:36px;border-radius:50%;background:#cfe2f1}
.about-title{position:absolute;left:510px;top:182px;width:94px;font-size:9px;line-height:1.45}
.about-text{position:absolute;left:475px;top:226px;width:120px;font-size:6px;line-height:1.9}

.legal{position:absolute;left:0;top:1164px;width:608px;height:36px;background:var(--footer-dark);color:var(--white);font-size:6.5px}
.legal nav{position:absolute;left:19px;top:14px;display:flex;gap:9px}
.legal .copy{position:absolute;right:16px;top:14px}
</style>
</head>
<body>
<div class="page">

  <header class="header">
    <div class="brand"><span class="brand-mark"></span><span class="brand-name">Haiyun Cruises</span></div>
    <div class="brand-url">www.haiyuncruise.example</div>
    <div class="account">
      <a href="#">Sign In</a><span>|</span><a href="#">Signup</a>
      <span class="lang"><i></i>English ▾</span>
      <span class="social"><span></span><span></span><span></span></span>
    </div>
    <div class="phone">1-800-555-0142</div>
    <div class="call">Call Us Today!</div>
  </header>

  <nav class="nav">
    <a href="#" style="left:16px">HOME</a>
    <a href="#" style="left:63px">DESTINATIONS</a>
    <a href="#" style="left:138px">CRUISE LINES</a>
    <a href="#" style="left:208px">LAND VACATIONS</a>
    <a href="#" style="left:292px">ABOUT CRUISING</a>
    <a href="#" style="left:376px">DEALS</a>
    <a href="#" style="left:423px">REQUEST QUOTE</a>
    <div class="search">SEARCH :
      <svg width="9" height="9" viewBox="0 0 10 10"><circle cx="4" cy="4" r="3" fill="none" stroke="#8b9196" stroke-width="1.2"/><line x1="6.3" y1="6.3" x2="9" y2="9" stroke="#8b9196" stroke-width="1.3"/></svg>
    </div>
  </nav>

  <section class="hero" role="img" aria-label="Two hikers with backpacks on a mountain summit photographing a green valley under a blue sky">
    <div class="hero-tag"><span class="l1">Cruise Vacations</span><span class="l2">&amp; So much more...</span></div>
    <span class="arrow" style="left:10px"></span>
    <span class="arrow" style="left:585px"></span>

    <form class="finder">
      <h2>FIND YOUR CRUISE</h2>
      <div class="rule"></div>
      <label style="left:13px;top:44px">Destination</label>
      <div class="select" style="left:13px;top:54px;width:149px">Cruise to nowhere</div>
      <label style="left:13px;top:81px">Length</label>
      <label style="left:93px;top:81px">Month</label>
      <div class="select" style="left:13px;top:91px;width:69px">Any length</div>
      <div class="select" style="left:93px;top:91px;width:69px">Any month</div>
      <label style="left:13px;top:118px">Cruise line</label>
      <div class="select" style="left:13px;top:128px;width:149px">Carnelia cruise lines</div>
      <label style="left:0;top:155px;width:172px;text-align:center;font-size:7px;font-weight:700">Number of travelers</label>
      <label style="left:13px;top:177px">Age 25+</label>
      <label style="left:93px;top:177px">Age 0 to 24</label>
      <div class="select" style="left:13px;top:187px;width:69px">2</div>
      <div class="select" style="left:93px;top:187px;width:69px">0</div>
      <div class="senior"><i></i>CHECK FOR SENIOR RATES</div>
      <div class="btn-search">SEARCH CRUISES</div>
    </form>
  </section>

  <section class="band">
    <div class="tab active" style="left:10px;width:92px">BOOK WITH US</div>
    <div class="tab" style="left:96px;width:68px">DEALS</div>
    <div class="tab" style="left:160px;width:80px">PACKAGES</div>
    <div class="tab" style="left:236px;width:66px">NEWS</div>
    <div class="tab" style="left:298px;width:120px">FIRST TIME CRUISER?</div>

    <div class="tab-body">
      <div class="photo-couple" role="img" aria-label="A couple sitting on a white ledge looking out over a turquoise sea"></div>
      <div class="photo-shadow"></div>
      <div class="promise">
        <h3>OUR PROMISE</h3>
        <p>Deal with the cruise experts to find and book your next dream getaway for less. Exceptional savings and value await.</p>
        <ul>
          <li><svg width="8" height="7" viewBox="0 0 8 7"><path d="M0.5 3.5 L3 6 L7.5 0.8" fill="none" stroke="#6aae2b" stroke-width="1.5"/></svg>Deal with the cruise experts</li>
          <li><svg width="8" height="7" viewBox="0 0 8 7"><path d="M0.5 3.5 L3 6 L7.5 0.8" fill="none" stroke="#6aae2b" stroke-width="1.5"/></svg>Deal with the cruise experts to findbook</li>
          <li><svg width="8" height="7" viewBox="0 0 8 7"><path d="M0.5 3.5 L3 6 L7.5 0.8" fill="none" stroke="#6aae2b" stroke-width="1.5"/></svg>Deal with the cruise</li>
          <li><svg width="8" height="7" viewBox="0 0 8 7"><path d="M0.5 3.5 L3 6 L7.5 0.8" fill="none" stroke="#6aae2b" stroke-width="1.5"/></svg>Deal with the cruise experts</li>
          <li><svg width="8" height="7" viewBox="0 0 8 7"><path d="M0.5 3.5 L3 6 L7.5 0.8" fill="none" stroke="#6aae2b" stroke-width="1.5"/></svg>Deal with the cruise experts Deal with</li>
        </ul>
      </div>
      <div class="dots"><i></i><i></i><i></i><i></i><i></i></div>
    </div>

    <div class="deals">Best Deals<br>Promotions<br>Packages</div>
    <p class="signup-note">Sign up for our newsletter and receive our best deals in your inbox.</p>
    <div class="field" style="left:478px;top:170px;width:119px">First Name :</div>
    <div class="field" style="left:478px;top:193px;width:119px">Email :</div>
    <div class="field" style="left:478px;top:217px;width:119px">Postal Code :</div>
    <div class="field" style="left:478px;top:240px;width:119px">Postal/Zip :</div>
    <div class="btn-red">Subscribe</div>
    <a class="contest" href="#" style="left:548px;top:269px">Contest Rules</a>
  </section>

  <footer class="footer">
    <h4 style="left:20px;top:20px">Popular Cruise Lines</h4>
    <ul style="left:20px;top:38px">
      <li>Carnelia Cruise Lines</li><li>Celestra Cruises</li><li>Coralto Cruises</li>
      <li>Dunmore Cruise Line</li><li>Hollis Amerigo Line</li><li>MVR Cruises</li>
      <li>Nordvik Cruise Line</li><li>Principia Cruises</li><li>Regal Tidewater International</li>
    </ul>
    <a class="more" href="#" style="left:20px;top:171px">See all cruise lines »</a>

    <h4 style="left:20px;top:206px">Popular Destinations</h4>
    <ul style="left:20px;top:224px">
      <li>Alaska</li><li>Caribbean</li><li>Europe</li><li>Hawaii</li><li>Mexico</li>
    </ul>
    <a class="more" href="#" style="left:20px;top:299px">See all cruise Destinations »</a>

    <h4 style="left:20px;top:330px">Cruise by Type</h4>
    <ul style="left:20px;top:348px">
      <li>Popular Cruises</li><li>Luxury Cruises</li><li>River Cruises</li>
    </ul>
    <a class="more" href="#" style="left:20px;top:399px">See All Cruise Types»</a>

    <h4 style="left:175px;top:20px">Land Vacations</h4>
    <ul style="left:175px;top:38px">
      <li>Hotels</li><li>Flights</li><li>Car Rentals</li><li>Vacation Packages</li><li>Shore Excursions</li>
    </ul>
    <a class="more" href="#" style="left:175px;top:115px">See All Land Vacations »</a>

    <h4 style="left:175px;top:150px">All About Cruising</h4>
    <ul style="left:175px;top:168px">
      <li>Frequently Asked Questions</li><li>First Time Cruisers</li><li>Value Comparison</li>
      <li>Cruising with Kids</li><li>Vacation Packing Guide</li><li>Onboard Activities</li>
      <li>Theme Cruises</li><li>Special Event Cruises</li>
    </ul>
    <a class="more" href="#" style="left:175px;top:284px">See All About Cruising »</a>

    <div class="community">
      <h4 style="left:12px;top:10px">Join Our Community</h4>
      <a class="sbtn" href="#" style="top:35px"><i></i>Sign in with Plazanet</a>
      <a class="sbtn" href="#" style="top:55px"><i></i>Sign in with Chirpline</a>
      <h4 style="left:12px;top:86px">Free E-Newsletter</h4>
      <p>Want great deals delivered to your inbox? Sign up for our free newsletter and you could win a free cruise for two!</p>
      <div class="field" style="top:148px">First Name :</div>
      <div class="field" style="top:171px">Email :</div>
      <div class="field" style="top:195px">Postal Code :</div>
      <div class="field" style="top:218px">Postal/Zip :</div>
      <div class="btn-blue" style="top:242px">Subscribe</div>
      <a class="contest" href="#" style="left:84px;top:246px;color:#fff">Contest Rules</a>
    </div>

    <h4 style="left:469px;top:23px">Contact Us today</h4>
    <div class="contact-card"><i></i></div>
    <div class="abs" style="left:469px;top:114px;font-size:10px">Haiyun Cruises</div>
    <div class="contact-line" style="top:134px">
      <svg width="9" height="8" viewBox="0 0 10 8"><path d="M1 3 Q5 -1 9 3 L8 4 L6.5 3 L6.5 2 Q5 1.5 3.5 2 L3.5 3 L2 4 Z M2.5 5 H7.5 V7.5 H2.5 Z" fill="#fff"/></svg>1-800-555-0142</div>
    <div class="contact-line" style="top:150px">
      <svg width="9" height="7" viewBox="0 0 9 7"><rect x="0.5" y="0.5" width="8" height="6" fill="#fff"/><path d="M0.5 0.5 L4.5 4 L8.5 0.5" fill="none" stroke="#3b78ad" stroke-width="0.8"/></svg>Click to Contact Me</div>
    <div class="about-mark"></div>
    <div class="about-title">About<br>haiyuncruise.example</div>
    <p class="about-text">Established in 1987, Trekvista® Harbor Fleet Desk® is a global leader in the marketing and sales of more...</p>
  </footer>

  <div class="legal">
    <nav><a href="#">Terms of Use</a><span>|</span><a href="#">Privacy</a><span>|</span><a href="#">Legal</a><span>|</span><a href="#">Site Map</a><span>|</span><a href="#">Reset Location</a><span>|</span><a href="#">Feedback</a></nav>
    <div class="copy">© 2013. Haiyun Cruises. All rights reserved.</div>
  </div>

</div>
</body>
</html>
```